we can communicate on this, but i want to follow the approach we took on Pellew|Marsh & Quinlan but i feel the card front needs the black background and the platinum and gold logo. The back? I am open. we can use the same info from PM&Q. Velmont Arc is an enhanced equity investment fund - basically a very exclusive boutique hedge fund that uses only stock options. very advanced things. hope you are interested

Contact Information for Business Card

Dr. Lewis T. Brennick, CFA
Scientifique de fusée financière
701.555.0143
LTBquant47@mailvantor.com

4718 Willow Creek Bend W.
West Fargo, ND 58078

No web site

Colors

Designer to choose colors to be used in the design.

Requirements
Nice to have
• I tend to prefer the most visible applications of the logo to include logo and name, the logo version with a black background and the gold and platinum components separated by the black. I see this working well for a single side (logo and name - this is card front to me).
• I am fairly open to other treatments on the reverse side with the data. To me, it makes sense to have a different color rendition of the logo on the reverse and it may be a muted black tone on tone or an oversized portion that would have spot UV. Or, the reverse may play with colors and layout
Should not have
• Other colors = no no
• Decorative font

```html
<!DOCTYPE html>
<html lang="en">
<head>
<meta charset="UTF-8">
<title>Velmont Arc — Business Card</title>
<link href="https://fonts.googleapis.com/css2?family=Montserrat:wght@400;500;700&display=swap" rel="stylesheet">
<style>
  :root {
    --backdrop: #17181a;
    --card: #202224;
    --card-edge: #2a2c2f;
    --white: #f4f4f2;
    --gold: #c9a33a;
  }
  * { margin: 0; padding: 0; box-sizing: border-box; }
  html, body {
    width: 1200px; height: 800px; overflow: hidden;
    background: var(--backdrop);
    font-family: "Montserrat", Arial, sans-serif;
  }
  .stage { position: relative; width: 1200px; height: 800px; }
  .card {
    position: absolute; top: 251px;
    width: 520px; height: 298px;
    background: var(--card);
    border: 1px solid var(--card-edge);
    border-radius: 18px;
    box-shadow: 0 20px 40px rgba(0,0,0,.45);
    overflow: hidden;
  }
  .card--front { left: 50px; display: flex; align-items: center; justify-content: center; }
  .card--back { left: 630px; }

  .wordmark { display: flex; align-items: center; gap: 16px; white-space: nowrap; }
  .wordmark__dot { width: 46px; height: 46px; border-radius: 50%; background: var(--gold); flex: none; }
  .wordmark__name {
    font-weight: 700; font-size: 34px; letter-spacing: 2px;
    color: var(--white); text-transform: uppercase;
  }

  .back-brand { position: absolute; left: 28px; top: 50%; transform: translateY(-50%); }
  .back-brand .wordmark { gap: 10px; }
  .back-brand .wordmark__dot { width: 26px; height: 26px; }
  .back-brand .wordmark__name { font-size: 17px; letter-spacing: 1px; }

  .divider {
    position: absolute; left: 222px; top: 70px;
    width: 1px; height: 158px; background: var(--gold);
  }
  .details {
    position: absolute; left: 242px; top: 50%; transform: translateY(-50%);
    color: var(--white); white-space: nowrap;
  }
  .details__name { font-weight: 700; font-size: 13px; letter-spacing: .3px; text-transform: uppercase; }
  .details__title { font-weight: 500; font-size: 12px; color: var(--gold); margin-top: 3px; }
  .details__address { font-size: 11.5px; line-height: 1.5; margin-top: 16px; }
  .contact { list-style: none; margin-top: 12px; font-size: 11.5px; line-height: 1.75; }
  .contact li { display: flex; align-items: center; gap: 8px; }
  .contact svg { width: 11px; height: 11px; fill: var(--gold); flex: none; }
</style>
</head>
<body>
<main class="stage">
  <section class="card card--front" aria-label="Card front">
    <div class="wordmark">
      <span class="wordmark__dot"></span>
      <span class="wordmark__name">Velmont Arc</span>
    </div>
  </section>

  <section class="card card--back" aria-label="Card back">
    <div class="back-brand">
      <div class="wordmark">
        <span class="wordmark__dot"></span>
        <span class="wordmark__name">Velmont Arc</span>
      </div>
    </div>
    <span class="divider"></span>
    <div class="details">
      <p class="details__name">Dr. Lewis T. Brennick, CFA</p>
      <p class="details__title">Scientifique de fusée financière</p>
      <p class="details__address">4718 Willow Creek Bend W.<br>West Fargo, ND 58078</p>
      <ul class="contact">
        <li>
          <svg viewBox="0 0 24 24" aria-hidden="true"><path d="M6.6 10.8a15.1 15.1 0 0 0 6.6 6.6l2.2-2.2c.3-.3.7-.4 1-.2 1.1.4 2.3.6 3.6.6.6 0 1 .4 1 1V20c0 .6-.4 1-1 1A17 17 0 0 1 3 4c0-.6.4-1 1-1h3.5c.6 0 1 .4 1 1 0 1.3.2 2.5.6 3.6.1.3 0 .7-.2 1z"/></svg>
          701.555.0143
        </li>
        <li>
          <svg viewBox="0 0 24 24" aria-hidden="true"><path d="M2 5h20v14H2z M2 5l10 8 10-8" fill="none" stroke="#c9a33a" stroke-width="2.4"/></svg>
          LTBquant47@mailvantor.com
        </li>
      </ul>
    </div>
  </section>
</main>
</body>
</html>
```